Car transport business

We need a new business card design. Attached is our old card sample. I would just like to adjust the logo colors (blue and red) to be brighter. I changed my name to the brighter red and the word dispatcher to a brighter blue as an example. But you can adjust those colors further. And then perhaps you can use the same colors for the card design but use your imagination.

As a suggestion so the card stands out I would like to add a clip art of car carrier truck. Attached are examples of that as well

```html
<!DOCTYPE html>
<html lang="en">
<head>
<meta charset="UTF-8">
<title>Swift Haul – Business Card</title>
<link rel="stylesheet" href="https://fonts.googleapis.com/css2?family=Roboto:wght@400;500;700&display=swap">
<style>
  :root {
    --stage: #2a2b2d;
    --card-light: #ffffff;
    --card-dark: #18191b;
    --gloss-high: #55575c;
    --gloss-mid: #303236;
    --gloss-low: #1c1d20;
    --brand-blue: #1a6fc9;
    --brand-red: #e8161f;
    --ink: #1d1d1f;
    --rule: #c9c9c9;
  }
  * { box-sizing: border-box; margin: 0; padding: 0; }
  html, body {
    width: 1200px;
    height: 1108px;
    overflow: hidden;
    background: var(--stage);
    font-family: "Roboto", Arial, sans-serif;
  }
  .stage {
    width: 1200px;
    height: 1108px;
    display: flex;
    align-items: center;
    justify-content: center;
    gap: 70px;
  }
  .card {
    width: 400px;
    height: 660px;
    border-radius: 26px;
    position: relative;
    overflow: hidden;
  }
  .card--front {
    background: var(--card-light);
    display: flex;
    flex-direction: column;
    align-items: center;
  }
  .brand {
    margin-top: 150px;
    text-align: center;
  }
  .brand__name {
    display: flex;
    align-items: center;
    justify-content: center;
    gap: 12px;
    font-weight: 700;
    font-size: 46px;
    letter-spacing: 1px;
    color: var(--brand-blue);
    text-transform: uppercase;
  }
  .brand__dot {
    width: 18px;
    height: 18px;
    border-radius: 50%;
    background: var(--brand-red);
  }
  .brand__tagline {
    margin-top: 6px;
    font-size: 11.5px;
    letter-spacing: 2.6px;
    color: var(--brand-blue);
    text-transform: uppercase;
  }
  .person {
    margin-top: 190px;
    text-align: center;
  }
  .person__name {
    font-size: 34px;
    font-weight: 500;
    text-transform: uppercase;
    letter-spacing: 0.5px;
  }
  .person__first { color: var(--brand-blue); }
  .person__last { color: var(--brand-red); }
  .person__role {
    margin-top: 2px;
    font-size: 19px;
    color: var(--brand-blue);
    text-transform: uppercase;
  }
  .divider {
    width: 100px;
    height: 1px;
    background: var(--rule);
    margin: 22px 0 20px;
  }
  .contact {
    list-style: none;
    text-align: center;
    font-size: 19px;
    line-height: 1.28;
    color: var(--ink);
  }
  .card--back {
    background: var(--card-dark);
  }
  .back__pattern {
    position: absolute;
    inset: 0;
    background:
      radial-gradient(ellipse 75% 60% at 85% 12%, var(--gloss-high) 0%, rgba(85, 87, 92, 0) 70%),
      radial-gradient(ellipse 70% 55% at 30% 45%, var(--gloss-mid) 0%, rgba(48, 50, 54, 0) 75%),
      linear-gradient(200deg, var(--gloss-mid) 0%, var(--gloss-low) 60%, var(--card-dark) 100%);
  }
  .back__brand {
    position: absolute;
    right: 76px;
    bottom: 150px;
    display: flex;
    align-items: center;
    gap: 8px;
    font-weight: 700;
    font-size: 18px;
    color: var(--brand-blue);
    text-transform: uppercase;
  }
  .back__dot {
    width: 10px;
    height: 10px;
    border-radius: 50%;
    background: var(--brand-red);
  }
</style>
</head>
<body>
  <main class="stage">
    <section class="card card--front">
      <div class="brand">
        <div class="brand__name"><span class="brand__dot"></span>Swift Haul</div>
        <p class="brand__tagline">The Auto Transport Professionals</p>
      </div>
      <div class="person">
        <h1 class="person__name"><span class="person__first">Leo</span> <span class="person__last">Varga</span></h1>
        <p class="person__role">Diapatcher</p>
      </div>
      <div class="divider"></div>
      <ul class="contact">
        <li>555-210-4837</li>
        <li>555-210-9162</li>
        <li>swifthaulinc@example.com</li>
      </ul>
    </section>

    <section class="card card--back">
      <div class="back__pattern" role="img" aria-label="Full-bleed tone-on-tone repeating pattern of the company car mark in spot gloss on black, brighter toward the top right"></div>
      <div class="back__brand"><span class="back__dot"></span>Swift Haul</div>
    </section>
  </main>
</body>
</html>
```